Elegant, High End Integrated Wellness Healthcare Practice

We need a brochure designed for an integrated mind-body wellness healthcare practice (www.quellarivecare.com) . This brochure will be used when we cold call prospects (physicians to refer to our office, and potential consumers to utilize our services). Our practice is geographically located in the middle Tennessee USA region, although we have plans to become an international company as many of our offerings can be accessed anywhere in the world. Ultimately our goal is to have this brochure used as a leave-behind in an effort to introduce our integrated offerings to increase market share. The final product brochure should be both elegant and serious, with clean lines but also convey warmth and trust, as individuals who are coming for our services have usually struggled with their health for a significant amount of time before finding our practice.
Updates

The design brief was very specific about providing a high-end science-based 2-page brochure (not flier). Several designs submitted were fliers. The other designs were heavy on yoga or "woo woo" non-science-based looking pictures. This is a flier to appeal to physicians and other healthcare providers. Therefore the design must speak science and evidence-based methods of mind and body wellness care. I would also like to appeal to the other designers I paid extra for their submissions and who have indicated they will "respond in the coming days."

```html
<!DOCTYPE html>
<html lang="en">
<head>
<meta charset="utf-8">
<title>Quellarive Care Brochure</title>
<link href="https://fonts.googleapis.com/css2?family=Playfair+Display:wght@600;700&family=Poppins:wght@300;400;500&display=swap" rel="stylesheet">
<style>
:root{
  --bg:#d9d9d9;
  --green:#6dae36;
  --green-soft:#e6f3cf;
  --green-pale:#f2f9e6;
  --dark:#1f3309;
  --dark-2:#2a4210;
  --ink:#2b2b2b;
  --grey-box:#f1f1f1;
  --white:#ffffff;
}
*{box-sizing:border-box;margin:0;padding:0}
html,body{width:1200px;height:1200px;overflow:hidden;background:var(--bg)}
body{position:relative;font-family:'Poppins',sans-serif;color:var(--ink)}
.spread{position:absolute;width:570px;height:404px;display:flex;box-shadow:0 10px 18px rgba(0,0,0,.18)}
.panel{position:relative;width:285px;height:404px;overflow:hidden}
.serif{font-family:'Playfair Display',serif}
.photo{position:absolute;z-index:1}
.accent{color:var(--green)}

/* cover */
.cover .panel{background:linear-gradient(160deg,#eef7dd,var(--green-soft))}
.brand{position:absolute;display:flex;align-items:center;gap:6px;z-index:2}
.brand-dot{width:26px;height:26px;border-radius:50%;background:var(--dark)}
.brand-name{font-family:'Playfair Display',serif;font-weight:600;font-variant:small-caps;color:var(--dark);font-size:13px;line-height:1.15}
.contact{position:absolute;left:22px;top:295px;font-size:8.6px;color:var(--ink);line-height:1.35;z-index:2}
.contact li{list-style:none;display:flex;gap:8px;margin-bottom:5px}
.contact svg{flex:none;margin-top:1px}
.cover-title{position:absolute;left:0;width:285px;top:282px;text-align:center;font-family:'Playfair Display',serif;font-weight:700;color:var(--dark);font-size:20px;line-height:1.05;z-index:2}
.cover-title span{font-size:24px}
.tagline{position:absolute;left:0;width:285px;top:343px;text-align:center;font-size:10.5px;font-weight:500;color:var(--dark);z-index:2}
.url{position:absolute;left:0;width:285px;top:376px;text-align:center;font-family:'Playfair Display',serif;font-size:10px;color:var(--dark);z-index:2}

/* welcome + services */
.intro .panel{background:var(--white)}
.corner{position:absolute;left:-22px;top:-22px;width:66px;height:66px;border-radius:50%;background:var(--green)}
.h2{font-family:'Playfair Display',serif;font-weight:700;color:var(--dark);font-size:14px;line-height:1.05;z-index:2}
.welcome-title{position:absolute;left:20px;top:22px}
.body-text{font-size:6.6px;line-height:1.45;color:var(--ink)}
.welcome-text{position:absolute;left:20px;top:61px;width:205px;z-index:2}
.welcome-text p{margin-bottom:6px}
.welcome-text p.narrow{width:118px}
.band{position:absolute;left:0;top:247px;width:285px;height:157px;background:var(--green)}
.band-text{position:absolute;left:20px;top:20px;width:175px;font-size:6.6px;line-height:1.45;color:var(--white);z-index:2}
.band-text b{font-weight:500}
.services-title{position:absolute;left:20px;top:22px}
.services-intro{position:absolute;left:20px;top:43px;width:250px}
.grid{position:absolute;left:20px;top:76px;display:grid;grid-template-columns:repeat(3,80px);grid-auto-rows:25.5px;column-gap:6px;row-gap:6.3px}
.svc{display:flex;align-items:center;padding:0 7px;font-size:5.8px;line-height:1.2}
.svc.g{background:var(--green);color:var(--white)}
.svc.d{background:var(--dark);color:var(--white)}
.svc.l{background:var(--grey-box);color:var(--ink)}

/* team + treat */
.team{background:var(--dark)}
.team .h2{color:var(--white)}
.team-title{position:absolute;left:20px;top:22px}
.team-intro{position:absolute;left:20px;top:42px;width:245px;color:#e9f0de}
.member-photo{position:absolute;width:80px;height:86px;border-radius:50%;background:radial-gradient(circle at 50% 45%,#d8c3b0,#7b8fa6 75%);box-shadow:-6px 0 0 var(--green)}
.member{position:absolute;width:145px;color:#e9f0de}
.member h3{font-family:'Playfair Display',serif;font-weight:700;color:var(--white);font-size:10px;margin-bottom:3px}
.treat{background:var(--white)}
.treat-title{position:absolute;left:20px;top:22px}
.treat-intro{position:absolute;left:20px;top:42px;width:245px}
.box{position:absolute;left:20px;width:247px;padding:8px 9px}
.box > *{position:relative;z-index:2}
.box h4{font-family:'Playfair Display',serif;font-weight:700;font-size:9.5px;line-height:1.1;margin-bottom:5px}
.box ul{list-style:none;font-size:6.4px;line-height:1.5}
.box.dark{background:var(--dark);color:var(--white)}
.box.green{background:var(--green);color:var(--white)}
.box.light{background:var(--grey-box);color:var(--ink)}
.cols{display:flex;gap:12px}
.cols ul{width:108px}
</style>
</head>
<body>

<section class="spread cover" style="left:20px;top:176px">
  <div class="panel">
    <div class="photo" role="img" aria-label="Woman seated cross-legged holding a singing bowl" style="left:95px;top:18px;width:180px;height:270px;background:radial-gradient(ellipse at 55% 50%,#d9c6b3 0%,#e4dccd 45%,rgba(230,243,207,0) 72%)"></div>
    <div class="brand" style="left:22px;top:240px">
      <div class="brand-dot"></div>
      <div class="brand-name">Quellarive<br>Care</div>
    </div>
    <ul class="contact">
      <li><svg width="9" height="9" viewBox="0 0 24 24"><path fill="#6dae36" d="M6.6 10.8a15 15 0 0 0 6.6 6.6l2.2-2.2c.3-.3.7-.4 1-.2 1.1.4 2.3.6 3.6.6.6 0 1 .4 1 1V20c0 .6-.4 1-1 1C10.6 21 3 13.4 3 4c0-.6.4-1 1-1h3.5c.6 0 1 .4 1 1 0 1.3.2 2.5.6 3.6.1.3 0 .7-.2 1z"/></svg>+1 615 555 0142</li>
      <li><svg width="9" height="10" viewBox="0 0 24 24"><path fill="#6dae36" d="M12 2a7 7 0 0 0-7 7c0 5.2 7 13 7 13s7-7.8 7-13a7 7 0 0 0-7-7zm0 9.5A2.5 2.5 0 1 1 12 6.5a2.5 2.5 0 0 1 0 5z"/></svg><span>480 Alder Bend Rd, Riverton,<br>TN 37000, United States</span></li>
      <li><svg width="9" height="9" viewBox="0 0 24 24"><rect x="3" y="5" width="18" height="16" rx="2" fill="none" stroke="#6dae36" stroke-width="2.4"/><path stroke="#6dae36" stroke-width="2.4" d="M3 10h18M8 3v4M16 3v4"/></svg><span>Monday - Friday<br>7am - 8pm</span></li>
    </ul>
  </div>
  <div class="panel">
    <div class="brand" style="left:110px;top:20px">
      <div class="brand-dot" style="width:32px;height:32px"></div>
      <div class="brand-name" style="font-size:14px">Quellarive<br>Care</div>
    </div>
    <div class="photo" role="img" aria-label="Woman meditating in lotus pose with leaf illustrations" style="left:40px;top:72px;width:200px;height:200px;background:radial-gradient(ellipse at 50% 55%,#d9c6b3 0%,#e8e0cf 40%,rgba(230,243,207,0) 70%)"></div>
    <h1 class="cover-title">QUELLARIVE<br><span>CARE</span></h1>
    <p class="tagline">Discover a Better Way To Better You</p>
    <p class="url">www.quellarivecare.com</p>
  </div>
</section>

<section class="spread intro" style="left:610px;top:176px">
  <div class="panel">
    <div class="corner"></div>
    <h2 class="h2 welcome-title">Welcome to<br>Quellarive Care</h2>
    <div class="body-text welcome-text">
      <p>At <span class="accent">Quellarive Care</span> we facilitate body and <span class="accent">mind health</span> and <span class="accent">wellness</span> through an integrated functional approach to care. This method of personalized care appreciates you as a <span class="accent">unique</span> individual with distinct health circumstances. We tailor our body and mind approaches to address your specific health concerns.</p>
      <p class="narrow">Through the combination of <span class="accent">body</span> and <span class="accent">mind</span> interventions, we address concerns such as <span class="accent">Attention Deficit</span>, Distractibility and learning concerns, chronic pain and inflammation conditions, and mind health conditions such as anxiety, depression, panic, &amp; many more.</p>
    </div>
    <div class="photo" role="img" aria-label="Woman meditating seated on grass" style="left:146px;top:142px;width:134px;height:102px;border-radius:0 0 0 100%;background:linear-gradient(180deg,#ffffff 0%,#e9eef0 40%,#8fc54a 90%)"></div>
    <div class="band">
      <p class="band-text"><b>Quellarive Care</b> is different than traditional health practices. Our approach toward health and wellness looks at the whole person and the interaction of each aspect of your being with the other. We have <b>core values</b> that are the backbone of <b>effective integrated care.</b></p>
      <div class="photo" role="img" aria-label="Woman in a seated forward stretch" style="left:85px;top:70px;width:200px;height:87px;background:radial-gradient(ellipse at 55% 60%,#d8c3ad 0%,#c5b39c 35%,rgba(109,174,54,0) 70%)"></div>
    </div>
  </div>
  <div class="panel">
    <h2 class="h2 services-title">Our Services</h2>
    <p class="body-text services-intro">At <span class="accent">Quellarive Care</span> we facilitate body and mind <span class="accent">health</span> and <span class="accent">wellness</span> through an integrated functional approach to care.</p>
    <div class="grid">
      <div class="svc g">Sonal Brain<br>Care</div><div class="svc l">Functional<br>Medicine</div><div class="svc d">Healthy Lifestyle<br>Package</div>
      <div class="svc l">Light Therapy<br>for Pain</div><div class="svc d">Wellness<br>Package</div><div class="svc g">Mind<br>Health</div>
      <div class="svc d">Body<br>Health</div><div class="svc g">Sleep<br>Restoration</div><div class="svc l">Whole Body<br>Wellness</div>
      <div class="svc g">Nutrition<br>Wellness</div><div class="svc l">360° Integrative<br>Wellness</div><div class="svc d">Brain Wave<br>Mapping</div>
      <div class="svc l">ADHD &amp; EMDR</div><div class="svc d">Stress<br>Management</div><div class="svc g">Body Composition<br>Scan</div>
      <div class="svc d">Lab Testing</div><div class="svc g">Anxiety<br>Treatment</div><div class="svc l">Irritable Bowel<br>Syndrome</div>
      <div class="svc g">Depression</div><div class="svc l">Nutritional<br>Coach</div><div class="svc d">PTSD</div>
      <div class="svc l">Emotional Freedom<br>Techniques</div><div class="svc d">Meditation</div><div class="svc g">Fibromyalgia</div>
      <div class="svc d">Inflamation<br>&amp; Body Pain</div><div class="svc g">Solution Focused<br>Sleep Therapy</div><div class="svc l">Metabolic<br>Breath Test</div>
      <div class="svc g">Nutraceuticals</div><div class="svc l">Gatroesophageal<br>Reflux Disease</div><div class="svc d">Heartburn</div>
    </div>
  </div>
</section>

<section class="spread" style="left:315px;top:626px">
  <div class="panel team">
    <h2 class="h2 team-title">Meet Our Team</h2>
    <p class="body-text team-intro">Meet the experienced team at Quellarive Care, we facilitate body &amp; mind health and wellness through an integrated functional approach to care that is unique to you.</p>
    <div class="member-photo" role="img" aria-label="Portrait of Dr. Nora Ellison" style="left:24px;top:84px"></div>
    <div class="member body-text" style="left:122px;top:100px">
      <h3>Dr. Nora Ellison</h3>
      <p>Dr. Nora Ellison has been a practicing clinical psychologist for 15+ years. She has seen first-hand that medication and psychotherapy are often not enough to make true change.</p>
    </div>
    <div class="member body-text" style="left:20px;top:210px;width:135px">
      <h3>Dr. Walter Pryce</h3>
      <p>Dr. Walter Pryce, Ph.D. has been practicing and is an experienced trusted psychologist in Riverton, Tennessee.</p>
    </div>
    <div class="member-photo" role="img" aria-label="Portrait of Dr. Walter Pryce" style="left:178px;top:188px"></div>
    <div class="member-photo" role="img" aria-label="Portrait of Marian Holt" style="left:24px;top:292px"></div>
    <div class="member body-text" style="left:122px;top:318px">
      <h3>Marian Holt</h3>
      <p>She has worked with children, adolescents and parents in various settings over the past 26 years.</p>
    </div>
  </div>
  <div class="panel treat">
    <h2 class="h2 treat-title">What We <span class="accent">Treat</span></h2>
    <p class="body-text treat-intro"><span class="accent">Quellarive Care</span> provides <span class="accent">treatment for</span> a full scope of <span class="accent">psychiatric &amp; cognitive</span> conditions, attention, distractibility, learning concerns, and various complex chronic conditions.</p>
    <div class="box dark" style="top:81px;height:84px">
      <h4>Psychiatric &amp; Cognitive Conditions</h4>
      <div class="cols">
        <ul><li>• Anxiety &amp; Depression</li><li>• Bipolar Disorder</li><li>• Eating Disorders</li><li>• Headaches &amp; Migraines</li></ul>
        <ul><li>Obsessive Compulsive Disorder</li><li>• Insomnia and Sleep Disturbances</li><li>• Trauma</li></ul>
      </div>
    </div>
    <div class="box green" style="top:173px;height:84px">
      <h4>Attention, Distractibility &amp;<br>Learning Concerns</h4>
      <ul><li>• Attention &amp; Hyperactivity</li><li>• Memory, Concentration, and Brain Fog</li><li>• Emotional Dysregulation</li></ul>
    </div>
    <div class="box light" style="top:266px;height:84px">
      <h4>Complex Chronic Conditions</h4>
      <ul><li>• Chronic Fatigue Syndrome</li><li>• Fibromyalgia</li><li>• Acid Reflux and Heartburn</li><li>• Irritable Bowel Syndrome</li></ul>
    </div>
    <div class="photo" role="img" aria-label="Woman in a standing split yoga pose" style="left:195px;top:140px;width:88px;height:262px;background:radial-gradient(ellipse at 60% 60%,rgba(216,195,173,.9) 0%,rgba(226,212,196,.6) 35%,rgba(255,255,255,0) 70%)"></div>
  </div>
</section>

</body>
</html>
```